Reach Crafters Unique Marketing Website Design

I am starting a new company that is a thought leader in the marketing consulting space. The company is called Reach Crafters. We intend to build a Wordpress site on the Astra Theme with the Spectra builder. Our goal is to become the leading voice that empowers high-ticket service business leaders to become Reach Crafters by equipping them with the cutting-edge frameworks and decision grade intelligence taught in leading business schools. What we are looking for is a website design that is clean and professional, making some use of white space well also being eye catching and distinctive in the consulting space. We will probably want to have a video on the homepage not in the hero section, but just below to explain the company and what we do. Our tagline is "Be found. Be chosen." I have attached a brand guide with some messaging, our typography choices, and our color system. The full site will have a primary nav that is four pages - About us, Services, Insights (essentially a blog), and Contact Us. The goal of this project is to develop an art direction that I can give to a designer to build loads of new pages.

Target Market(s)

Business owners (mostly male) from 30-60 years old, looking to fix their sales and marketing funnel.

Industry/Entity Type

Marketing consulting

Font styles to use
Sans Serif

Requirements
Must have
• A clean, professional design that builds trust with owners of high-ticket service businesses. We need a space for explainer video, and sections that tell prospects what we do. Would also like to have a blog carousel.
Nice to have
• Social feeds, if possible. See attached documents for colors and fonts.
Should not have
• Our feel is professional enough to be trustworthy, but unique enough to be memorable. Cartoon ideas do not meet the professional test, and we do not want the website to appear feminine.

```html
<!DOCTYPE html>
<html lang="en">
<head>
<meta charset="utf-8">
<title>Reach Crafters — Be Found. Be Chosen.</title>
<link href="https://fonts.googleapis.com/css2?family=Oswald:wght@300;500;600&family=Poppins:wght@400;500;600;700&display=swap" rel="stylesheet">
<style>
:root{
  --blue:#2433f0;
  --navy:#0b1424;
  --ink:#111111;
  --text:#333333;
  --muted:#6b6b6b;
  --white:#ffffff;
  --grey-bg:#f1f1f1;
  --panel:#f4f4f4;
  --footer:#161616;
  --ice:#e6edf7;
  --green:#1f9d4c;
  --red:#d8253a;
}
*{box-sizing:border-box;margin:0;padding:0}
html,body{width:1200px;height:5226px;overflow:hidden}
body{font-family:'Poppins',sans-serif;color:var(--text);background:var(--white);position:relative}
.section{position:absolute;left:0;width:1200px;overflow:hidden}
.abs{position:absolute}
.head{font-family:'Oswald',sans-serif;font-weight:500;text-transform:uppercase;color:var(--ink);letter-spacing:.2px}
.center{text-align:center;left:0;width:1200px}
.blue{color:var(--blue)}
.btn{position:absolute;display:flex;align-items:center;justify-content:center;gap:6px;font-size:11.5px;font-weight:600;text-transform:uppercase;color:var(--white);background:var(--blue);text-decoration:none}
.btn svg{width:11px;height:11px}

/* hero */
.hero{top:0;height:791px;background:radial-gradient(ellipse 380px 330px at 870px 420px,#3a5c86 0%,#1a3150 45%,transparent 75%),linear-gradient(100deg,#0a1526 0%,#0f1f38 55%,#132846 100%)}
.hero-photo{position:absolute;left:640px;top:150px;width:480px;height:480px;border-radius:50%;background:radial-gradient(circle at 45% 45%,#6a2a1e 0%,#2b4e78 45%,#1a2d47 70%,transparent 72%)}
.logo{position:absolute;font-family:'Poppins',sans-serif;font-weight:600;color:var(--white);letter-spacing:.3px;white-space:nowrap}
.nav a{position:absolute;top:62px;font-size:12px;font-weight:600;color:var(--white);text-decoration:none;text-transform:uppercase}
.nav a.active{color:#4a66ff}
.nav .contact{top:54px;left:932px;width:122px;height:40px;display:flex;align-items:center;justify-content:center;background:var(--blue)}
.be{left:134px;top:232px;font-family:'Oswald',sans-serif;font-weight:500;font-size:134px;line-height:1;color:var(--white)}
.found{left:292px;top:244px;font-family:'Oswald',sans-serif;font-weight:300;font-size:48px;line-height:1;color:var(--white)}
.chosen{left:295px;top:311px;width:208px;height:47px;background:var(--blue);color:var(--white);font-family:'Oswald',sans-serif;font-weight:500;font-size:40px;letter-spacing:4px;display:flex;align-items:center;justify-content:center}
.hero-copy{left:142px;top:398px;width:470px;font-size:14px;line-height:29px;color:var(--white)}
.btn-outline{background:transparent;border:2px solid var(--white)}

/* story */
.story{top:791px;height:672px;background:var(--white)}
.story-photo{left:136px;top:126px;width:436px;height:436px;border-radius:50%;background:radial-gradient(circle at 20% 40%,#e0281d 0%,#8c1a1a 28%,#2a3448 60%,#1a2233 100%)}
.play{left:437px;top:106px;width:130px;height:130px;border-radius:50%;background:var(--white);display:flex;align-items:center;justify-content:center}
.play span{width:100px;height:100px;border-radius:50%;background:var(--blue);display:flex;align-items:center;justify-content:center}
.story-title{left:649px;top:150px;font-size:41px;line-height:48px}
.story-copy{left:649px;top:316px;width:430px;font-size:12.5px;line-height:26px;color:var(--text)}
.story-copy p+p{margin-top:26px}

/* disciplines */
.disciplines{top:1463px;height:611px;background:radial-gradient(ellipse 300px 220px at 300px 330px,#2a3a55 0%,transparent 70%),radial-gradient(ellipse 340px 240px at 980px 200px,#26344c 0%,transparent 70%),linear-gradient(180deg,#121a2a,#0d1422)}
.disc-title{top:112px;font-size:38px;color:var(--white)}
.disc{position:absolute;top:210px;width:390px;text-align:center;color:var(--white)}
.disc .icon{width:100px;height:100px;margin:0 auto;border-radius:50%;background:var(--white);border:5px solid #c7cfdb;display:flex;align-items:center;justify-content:center}
.disc h3{margin-top:30px;font-size:19px;font-weight:600;letter-spacing:.5px;text-transform:uppercase}
.disc p{margin-top:20px;font-size:12.5px;line-height:25px}

/* why */
.why{top:2074px;height:598px;background:var(--white)}
.why-title{top:126px;font-size:39px}
.why-copy{top:200px;font-size:12.5px;line-height:26px;color:var(--text)}
.pillar{position:absolute;top:326px;width:300px;text-align:center}
.pillar .icon{width:82px;height:82px;margin:0 auto;border-radius:50%;background:var(--ice);display:flex;align-items:center;justify-content:center}
.pillar .icon.solid{background:var(--blue)}
.pillar h4{margin-top:34px;font-size:15px;font-weight:600;color:var(--ink);line-height:26px}

/* testimonials */
.testimonials{top:2672px;height:544px;background:linear-gradient(180deg,#0f1a2e,#0a1222)}
.testi-title{top:96px;font-size:38px;color:var(--white)}
.card{position:absolute;background:var(--white);padding:20px 20px}
.card .who{display:flex;align-items:center;gap:14px}
.card .avatar{width:58px;height:58px;border-radius:50%;background:linear-gradient(135deg,#c9ced6,#8a919c)}
.card h5{font-size:14px;font-weight:600;color:var(--ink)}
.card small{display:block;font-size:11px;color:var(--blue);margin-top:6px}
.card p{margin-top:18px;font-size:11px;line-height:20px;color:#555}
.card.big p{font-size:12.5px;line-height:23px}
.arrow{position:absolute;width:42px;height:42px;border-radius:50%;background:var(--white);display:flex;align-items:center;justify-content:center}
.arrow.dark{background:var(--ink)}

/* leaders */
.leaders{top:3216px;height:761px;background:var(--white)}
.lead-title{top:116px;font-size:39px}
.lead-copy{top:192px;font-size:12.5px;line-height:26px;color:var(--text)}
.fit{position:absolute;left:235px;top:311px;width:727px;height:351px;background:var(--panel);border:1px solid #dcdcdc;display:flex}
.fit .col{flex:1}
.fit .col+.col{border-left:1px solid #d6d6d6}
.fit .col h6{height:55px;background:var(--blue);color:var(--white);font-size:14px;font-weight:600;display:flex;align-items:center;padding-left:40px}
.fit ul{list-style:none;padding:24px 40px 0 38px}
.fit li{display:flex;gap:10px;font-size:11.5px;line-height:21px;color:#444;margin-bottom:20px}
.fit li svg{flex:none;width:12px;height:12px;margin-top:4px}

/* insights */
.insights{top:3977px;height:726px;background:var(--grey-bg)}
.ins-title{top:110px;font-size:39px}
.post{position:absolute;top:199px;width:288px}
.post .thumb{position:relative;height:186px}
.post .date{position:absolute;right:0;bottom:10px;width:152px;height:34px;background:rgba(20,20,20,.85);color:var(--white);font-size:11px;display:flex;align-items:center;justify-content:center}
.post h5{margin-top:20px;font-size:13.5px;font-weight:600;line-height:26px;color:var(--ink)}
.post p{margin-top:14px;font-size:12px;line-height:22px;color:var(--muted)}

/* footer */
.footer{top:4703px;height:523px;background:var(--footer)}
.cta{position:absolute;left:95px;top:4596px;width:1017px;height:249px;background:var(--blue);text-align:center;color:var(--white)}
.cta h2{margin-top:74px;font-size:38px;color:var(--white)}
.cta p{margin-top:10px;font-size:14px;font-weight:600}
.cta .btn{left:395px;top:179px;width:190px;height:41px;background:var(--footer)}
.foot-logo{top:4903px;font-size:34px}
.foot-tag{top:4964px;font-size:12px;font-weight:600;color:var(--white)}
.foot-rule{left:280px;top:5002px;width:642px;height:1px;background:#555}
.foot-nav{top:5028px;display:flex;justify-content:center;gap:24px;font-size:12px;font-weight:600;color:var(--white)}
.foot-contact{top:5074px;display:flex;justify-content:center;gap:50px;font-size:13px;font-weight:500;color:var(--white)}
.foot-contact span{display:flex;align-items:center;gap:8px}
.copyright{top:5126px;font-size:11px;color:var(--white)}
</style>
</head>
<body>

<header class="section hero">
  <div class="hero-photo" role="img" aria-label="Magnifying glass over glowing financial bar charts in blue light"></div>
  <div class="logo" style="left:142px;top:48px;font-size:33px">Reach Crafters</div>
  <nav class="nav">
    <a class="active" style="left:562px">Home</a>
    <a style="left:627px">About Us</a>
    <a style="left:718px">Our Services</a>
    <a style="left:840px">Insights</a>
    <a class="contact">Contact Us</a>
  </nav>
  <div class="abs be">BE</div>
  <div class="abs found">FOUND</div>
  <div class="abs chosen">CHOSEN</div>
  <p class="abs hero-copy">We bring buyer insight and decision design normally locked inside top-tier consulting firms and MBA programs to founders who actually need it.</p>
  <a class="btn" style="left:144px;top:520px;width:201px;height:43px">Explore the Playbook <svg viewBox="0 0 12 12"><circle cx="6" cy="6" r="6" fill="#fff"/><path d="M5 3.5 7.5 6 5 8.5" stroke="#2433f0" stroke-width="1.6" fill="none"/></svg></a>
  <a class="btn btn-outline" style="left:364px;top:520px;width:218px;height:43px">Start a Conversation <svg viewBox="0 0 12 12"><circle cx="6" cy="6" r="6" fill="#fff"/><path d="M5 3.5 7.5 6 5 8.5" stroke="#0b1424" stroke-width="1.6" fill="none"/></svg></a>
</header>

<section class="section story">
  <div class="abs story-photo" role="img" aria-label="Speaker in a navy suit presenting with a microphone in front of a red stage sign"></div>
  <div class="abs play"><span><svg width="30" height="30" viewBox="0 0 30 30"><path d="M9 5 25 15 9 25Z" fill="#fff"/></svg></span></div>
  <h2 class="abs head story-title">Most businesses are<br>losing deals in a place<br><span class="blue">they can’t see</span></h2>
  <div class="abs story-copy">
    <p>Between lead generation and closing sits a black box where deals slow down, stall, or quietly disappear. Most teams feel it—but can’t explain it. Reach Crafters exists to open that box.</p>
    <p>We diagnose what’s actually happening inside your buyer’s journey, then show you how to design trust-based buying experiences where saying yes feels safer than saying no.</p>
  </div>
  <a class="btn" style="left:651px;top:529px;width:162px;height:42px">Watch Now <svg viewBox="0 0 12 12"><circle cx="6" cy="6" r="6" fill="#fff"/><path d="M5 3.5 7.5 6 5 8.5" stroke="#2433f0" stroke-width="1.6" fill="none"/></svg></a>
</section>

<section class="section disciplines">
  <h2 class="abs head center disc-title">Two disciplines. One clear outcome.</h2>
  <div class="disc" style="left:103px">
    <div class="icon"><svg width="50" height="50" viewBox="0 0 50 50" fill="none" stroke="#2a3a6a" stroke-width="2"><path d="M8 42h34"/><rect x="12" y="30" width="5" height="12"/><rect x="21" y="24" width="5" height="18"/><rect x="30" y="18" width="5" height="24"/><path d="M10 26 20 18 28 22 40 10"/><path d="M34 10h6v6"/></svg></div>
    <h3>Buyer Insight</h3>
    <p>Before prescribing solutions, we gather reconnaissance. We diagnose reality—how buyers experience your process, where trust breaks down, and where revenue is leaking.<br>The output is a dossier: decision-grade intelligence, not opinions.</p>
  </div>
  <div class="disc" style="left:697px">
    <div class="icon"><svg width="50" height="50" viewBox="0 0 50 50" fill="none" stroke="#2a3a6a" stroke-width="2"><circle cx="25" cy="22" r="12"/><path d="M19 22h12M25 16v12"/><path d="M14 38h22M18 44h14"/><path d="M25 34v4"/></svg></div>
    <h3>Decision Design</h3>
    <p>Once reality is clear, we apply behavioral science to design the environment where high-stakes decisions get made.<br>The output is a design system—a Confidence Blueprint that reduces friction, builds motivation, and increases conversion efficiency.</p>
  </div>
</section>

<section class="section why">
  <h2 class="abs head center why-title">Why this isn’t <span class="blue">“Marketing Consulting”</span></h2>
  <p class="abs center why-copy">Most consultants focus on one slice of the problem.<br>Reach Crafters applies academic-grade behavioral science and commercial-grade systems<br>thinking to the full revenue engine. No funnels. No hacks. No execution theater.</p>
  <div class="pillar" style="left:133px">
    <div class="icon"><svg width="44" height="44" viewBox="0 0 44 44" fill="none" stroke="#3a4a7a" stroke-width="1.8"><path d="M6 38h32"/><rect x="10" y="26" width="4" height="12"/><rect x="18" y="20" width="4" height="18"/><rect x="26" y="14" width="4" height="24"/><path d="M8 22 18 14 26 18 36 8"/></svg></div>
    <h4>Marketing chases awareness</h4>
  </div>
  <div class="pillar" style="left:447px">
    <div class="icon solid"><svg width="44" height="44" viewBox="0 0 44 44" fill="none" stroke="#fff" stroke-width="1.8"><rect x="8" y="10" width="28" height="20" rx="2"/><path d="M14 36h16M22 30v6"/><path d="M13 24l6-6 5 4 7-7"/></svg></div>
    <h4>Sales chases closes</h4>
  </div>
  <div class="pillar" style="left:764px">
    <div class="icon"><svg width="44" height="44" viewBox="0 0 44 44" fill="none" stroke="#3a4a7a" stroke-width="1.8"><rect x="11" y="7" width="22" height="30" rx="2"/><path d="M16 15h12M16 21h12M16 27h8"/></svg></div>
    <h4>Customer success chases<br>Retention.</h4>
  </div>
</section>

<section class="section testimonials">
  <h2 class="abs head center testi-title">Our Testimonials</h2>
  <div class="arrow" style="left:61px;top:302px"><svg width="12" height="12" viewBox="0 0 12 12"><path d="M8 2 3 6 8 10Z" fill="#111"/></svg></div>
  <div class="card" style="left:152px;top:213px;width:268px;height:213px">
    <div class="who"><div class="avatar" role="img" aria-label="Client portrait"></div><div><h5>Daniel Corvin</h5><small>Satisfied Client in USA</small></div></div>
    <p>Lorem ipsum dolor sit amet, consectetur adipiscing elit, sed do eiusmod tempor incididunt ut labore et dolore magna aliqua. Ut enim ad minim veniam, quis nostrud exercitation ullamco</p>
  </div>
  <div class="card big" style="left:441px;top:196px;width:329px;height:250px;padding:24px 30px">
    <div class="who"><div class="avatar" style="width:64px;height:64px" role="img" aria-label="Client portrait"></div><div><h5>Nadia Whitlow</h5><small>Satisfied Client in USA</small></div></div>
    <p>Lorem ipsum dolor sit amet, consectetur adipiscing elit, sed do eiusmod tempor incididunt ut labore et dolore magna aliqua. Ut enim ad minim veniam, quis nostrud exercitation ullamco</p>
  </div>
  <div class="card" style="left:792px;top:213px;width:268px;height:213px">
    <div class="who"><div class="avatar" role="img" aria-label="Client portrait"></div><div><h5>Priya Talwen</h5><small>Satisfied Client in USA</small></div></div>
    <p>Lorem ipsum dolor sit amet, consectetur adipiscing elit, sed do eiusmod tempor incididunt ut labore et dolore magna aliqua. Ut enim ad minim veniam, quis nostrud exercitation ullamco</p>
  </div>
  <div class="arrow" style="left:1097px;top:302px"><svg width="12" height="12" viewBox="0 0 12 12"><path d="M4 2 9 6 4 10Z" fill="#111"/></svg></div>
</section>

<section class="section leaders">
  <h2 class="abs head center lead-title">Built for leaders who’ve <span class="blue">outgrown guesswork</span></h2>
  <p class="abs center lead-copy">You’ve built a business that works.<br>Now you’re scaling—and the old instincts don’t transfer cleanly. Deals take longer. Messaging<br>gets fuzzy. Teams work hard but can’t explain why outcomes vary.</p>
  <div class="fit">
    <div class="col">
      <h6>This is for you if you want:</h6>
      <ul>
        <li><svg viewBox="0 0 12 12"><circle cx="6" cy="6" r="6" fill="#1f9d4c"/><path d="M3.3 6.2 5.2 8 8.8 4.2" stroke="#fff" stroke-width="1.5" fill="none"/></svg>Predictable, repeatable growth without heroics</li>
        <li><svg viewBox="0 0 12 12"><circle cx="6" cy="6" r="6" fill="#1f9d4c"/><path d="M3.3 6.2 5.2 8 8.8 4.2" stroke="#fff" stroke-width="1.5" fill="none"/></svg>Clear visibility into why deals are won and lost</li>
        <li><svg viewBox="0 0 12 12"><circle cx="6" cy="6" r="6" fill="#1f9d4c"/><path d="M3.3 6.2 5.2 8 8.8 4.2" stroke="#fff" stroke-width="1.5" fill="none"/></svg>A shared language your marketing and sales teams actually use</li>
        <li><svg viewBox="0 0 12 12"><circle cx="6" cy="6" r="6" fill="#1f9d4c"/><path d="M3.3 6.2 5.2 8 8.8 4.2" stroke="#fff" stroke-width="1.5" fill="none"/></svg>Founder-independent systems that scale—and sell</li>
      </ul>
    </div>
    <div class="col">
      <h6>This is not for:</h6>
      <ul>
        <li><svg viewBox="0 0 12 12"><circle cx="6" cy="6" r="6" fill="#d8253a"/><path d="M4 4 8 8M8 4 4 8" stroke="#fff" stroke-width="1.5"/></svg>Low-cost, high-volume businesses</li>
        <li><svg viewBox="0 0 12 12"><circle cx="6" cy="6" r="6" fill="#d8253a"/><path d="M4 4 8 8M8 4 4 8" stroke="#fff" stroke-width="1.5"/></svg>Funnel agencies or execution outsourcing</li>
        <li><svg viewBox="0 0 12 12"><circle cx="6" cy="6" r="6" fill="#d8253a"/><path d="M4 4 8 8M8 4 4 8" stroke="#fff" stroke-width="1.5"/></svg>Anyone looking for “growth hacks”</li>
      </ul>
    </div>
  </div>
</section>

<section class="section insights">
  <h2 class="abs head center ins-title">Insights from inside <span class="blue">the revenue black box</span></h2>
  <div class="arrow dark" style="left:61px;top:301px"><svg width="12" height="12" viewBox="0 0 12 12"><path d="M8 2 3 6 8 10Z" fill="#fff"/></svg></div>
  <article class="post" style="left:144px">
    <div class="thumb" role="img" aria-label="Harbour bridge and waterfront at dusk" style="background:linear-gradient(180deg,#6f8fb8 0%,#c9a57a 55%,#2b3a52 100%)"><span class="date">Dec 25, 2026 | Tech</span></div>
    <h5>Building Smarter, Not Harder:<br>The Power of Modern Design &amp; Planning</h5>
    <p>Government unveils key reforms in taxation, infrastructure, and social services.</p>
  </article>
  <article class="post" style="left:454px">
    <div class="thumb" role="img" aria-label="Person standing on a city rooftop at sunset" style="background:linear-gradient(180deg,#4a5566 0%,#c88652 55%,#3a2f2a 100%)"><span class="date">Dec 25, 2026 | Sales</span></div>
    <h5>Why Quality Matters More Than Ever<br>Quality is not just a feature</h5>
    <p>Emerging tech companies contribute to employment and innovation in urban hubs.</p>
  </article>
  <article class="post" style="left:764px">
    <div class="thumb" role="img" aria-label="Glowing network map of a continent at night" style="background:radial-gradient(circle at 55% 45%,#2f6fa8 0%,#12304f 50%,#06121f 100%)"><span class="date">Dec 25, 2026 | Strategy</span></div>
    <h5>From Vision to Reality: Turning Ideas<br>Into Results</h5>
    <p>New programs support farmers facing extreme weather conditions across the country.</p>
  </article>
  <div class="arrow dark" style="left:1097px;top:301px"><svg width="12" height="12" viewBox="0 0 12 12"><path d="M4 2 9 6 4 10Z" fill="#fff"/></svg></div>
</section>

<footer class="section footer"></footer>
<div class="cta">
  <h2 class="head">Ready to take the next step?</h2>
  <p>From planning to execution, we’re here to turn your vision into reality.</p>
  <a class="btn">Talk to our team <svg viewBox="0 0 12 12"><circle cx="6" cy="6" r="6" fill="#fff"/><path d="M5 3.5 7.5 6 5 8.5" stroke="#161616" stroke-width="1.6" fill="none"/></svg></a>
</div>
<div class="logo center foot-logo" style="text-align:center">Reach Crafters</div>
<p class="abs center foot-tag" style="text-align:center">Decision-grade intelligence for high-ticket service businesses.</p>
<div class="abs foot-rule"></div>
<nav class="abs center foot-nav"><span>HOME</span><span>ABOUT US</span><span>OUR SERVICES</span><span>INSIGHTS</span><span>CONTACT US</span></nav>
<div class="abs center foot-contact">
  <span><svg width="14" height="11" viewBox="0 0 14 11"><rect width="14" height="11" rx="1" fill="#fff"/><path d="M1 1.5 7 6 13 1.5" stroke="#161616" stroke-width="1.3" fill="none"/></svg>hello@reachcrafters.com</span>
  <span><svg width="12" height="12" viewBox="0 0 24 24"><path d="M6.6 10.8a15.1 15.1 0 0 0 6.6 6.6l2.2-2.2c.3-.3.7-.4 1-.2 1.1.4 2.3.6 3.6.6.6 0 1 .4 1 1V20c0 .6-.4 1-1 1A17 17 0 0 1 3 4c0-.6.4-1 1-1h3.5c.6 0 1 .4 1 1 0 1.3.2 2.5.6 3.6.1.3 0 .7-.2 1z" fill="#fff"/></svg>+1 (555) 014 2290</span>
</div>
<p class="abs center copyright" style="text-align:center">Copyright@2026. All Rights Reserved</p>

</body>
</html>
```